Business Card Design for Property Development Company Director

I am looking for a professional and unforgettable business card design for our Director of our Property Development Company.
Please see attached .pptx file to find out what information to include. You don't have to follow the exact format shown in the file - I am interested to see your creative flair using the information provided.

```html
<!DOCTYPE html>
<html lang="en">
<head>
<meta charset="utf-8">
<title>Varnell Property Group – Business Card</title>
<link href="https://fonts.googleapis.com/css2?family=Arimo:wght@400;700&display=swap" rel="stylesheet">
<style>
  :root {
    --brand-blue: #0d56a6;
    --brand-grey: #5b5c5e;
    --paper: #ffffff;
    --backdrop: #1d1d20;
    --text-dark: #3a3a3c;
  }
  * { box-sizing: border-box; margin: 0; padding: 0; }
  html, body {
    width: 1200px; height: 800px; overflow: hidden;
    background: var(--backdrop);
    font-family: "Arimo", Arial, sans-serif;
  }
  .stage {
    width: 1200px; height: 800px;
    display: flex; align-items: center; justify-content: center; gap: 40px;
  }
  .card {
    width: 540px; height: 309px; position: relative;
    box-shadow: 0 10px 30px rgba(0,0,0,.45);
  }
  /* Front */
  .card--front {
    background: var(--brand-blue); color: var(--paper);
    display: flex; flex-direction: column; justify-content: center;
    padding: 0 52px;
  }
  .tagline {
    font-weight: 700; font-size: 17px; line-height: 1.35;
    text-transform: uppercase; letter-spacing: .3px;
    text-align: center;
  }
  .brand {
    display: flex; align-items: center; justify-content: center;
    gap: 12px; margin: 30px 0 30px;
  }
  .brand__square { width: 22px; height: 22px; background: var(--paper); }
  .brand__name {
    font-weight: 700; font-size: 26px; letter-spacing: 1px;
    text-transform: uppercase;
  }
  .invite { font-size: 12px; text-align: center; }
  .invite strong { font-weight: 700; text-transform: uppercase; }
  /* Back */
  .card--back {
    background: var(--paper);
    display: flex; align-items: center; padding: 0 36px;
  }
  .back-brand {
    width: 220px; display: flex; align-items: center; gap: 10px;
  }
  .back-brand .brand__square { background: var(--brand-blue); width: 26px; height: 26px; }
  .back-brand .brand__name { color: var(--brand-blue); font-size: 28px; }
  .divider {
    width: 2px; height: 120px; background: var(--brand-blue); margin: 0 26px 0 8px;
  }
  .contact { color: var(--text-dark); }
  .contact__name {
    font-weight: 700; font-size: 19px; text-transform: uppercase;
    color: var(--brand-grey);
  }
  .contact__name span { color: var(--brand-blue); }
  .contact__role { color: var(--brand-blue); font-size: 14px; margin-bottom: 12px; }
  .contact__list { list-style: none; font-size: 13px; line-height: 1.6; }
  .contact__list li { display: flex; align-items: center; gap: 8px; }
  .contact__list svg { width: 13px; height: 13px; fill: var(--brand-blue); flex: none; }
  .licence { color: var(--brand-blue); font-size: 12.5px; margin-top: 8px; }
</style>
</head>
<body>
<main class="stage">
  <section class="card card--front" aria-label="Business card front">
    <p class="tagline">Property Development<br>&amp; Site Acquisition Specialists</p>
    <div class="brand">
      <span class="brand__square"></span>
      <span class="brand__name">Varnell Property Group</span>
    </div>
    <p class="invite">Ask me about our <strong>Investment &amp; Partnership</strong> opportunities</p>
  </section>

  <section class="card card--back" aria-label="Business card back">
    <div class="back-brand">
      <span class="brand__square"></span>
      <span class="brand__name">Varnell</span>
    </div>
    <div class="divider"></div>
    <div class="contact">
      <p class="contact__name">Martin <span>Calloway</span></p>
      <p class="contact__role">Director</p>
      <ul class="contact__list">
        <li><svg viewBox="0 0 24 24" aria-hidden="true"><path d="M6.6 10.8a15 15 0 0 0 6.6 6.6l2.2-2.2a1 1 0 0 1 1-.25 11.4 11.4 0 0 0 3.6.57 1 1 0 0 1 1 1V20a1 1 0 0 1-1 1A17 17 0 0 1 3 4a1 1 0 0 1 1-1h3.5a1 1 0 0 1 1 1c0 1.25.2 2.45.57 3.57a1 1 0 0 1-.25 1z"/></svg>0400 123 456</li>
        <li><svg viewBox="0 0 24 24" aria-hidden="true"><path d="M2 5h20v14H2zm2 2v.5l8 5 8-5V7l-8 5z"/></svg>martin@varnell.com.au</li>
        <li><svg viewBox="0 0 24 24" aria-hidden="true"><path d="M12 2a10 10 0 1 0 0 20 10 10 0 0 0 0-20zm6.9 9h-3a15 15 0 0 0-1.3-5.6A8 8 0 0 1 18.9 11zM12 4c.9 1.3 1.7 3.7 1.9 7h-3.8C10.3 7.7 11.1 5.3 12 4zM9.4 5.4A15 15 0 0 0 8.1 11h-3a8 8 0 0 1 4.3-5.6zM5.1 13h3a15 15 0 0 0 1.3 5.6A8 8 0 0 1 5.1 13zM12 20c-.9-1.3-1.7-3.7-1.9-7h3.8c-.2 3.3-1 5.7-1.9 7zm2.6-1.4a15 15 0 0 0 1.3-5.6h3a8 8 0 0 1-4.3 5.6z"/></svg>www.varnell.com.au</li>
      </ul>
      <p class="licence">Real Estate Lic: 1234567 &amp; 1234568</p>
    </div>
  </section>
</main>
</body>
</html>
```